TALMORK

The business want a professional looking business card. We have a scetch we will add but want the extra upgrade, and would like more suggestions for variations of our business cards.

```html
<!DOCTYPE html>
<html lang="en">
<head>
<meta charset="utf-8">
<title>TALMORK — Business Cards</title>
<link rel="stylesheet" href="https://fonts.googleapis.com/css2?family=Marcellus&family=Poppins:wght@300;400&family=Cormorant+Garamond:wght@600&display=swap">
<style>
  :root {
    --stage: #2a2a2b;
    --card: #222222;
    --gold: #c9a44c;
    --gold-soft: #b8963f;
    --faint: #3a352a;
  }
  html, body {
    margin: 0;
    padding: 0;
    width: 1200px;
    height: 900px;
    overflow: hidden;
    background: var(--stage);
  }
  .canvas {
    position: relative;
    width: 1200px;
    height: 900px;
  }
  .card {
    position: absolute;
    width: 640px;
    height: 370px;
    background: var(--card);
    border-radius: 22px;
    box-shadow: 0 14px 30px rgba(0,0,0,0.45);
    overflow: hidden;
  }
  .card--front { left: 470px; top: 50px; }
  .card--back  { left: 110px; top: 470px; }

  .faint-mark {
    position: absolute;
    left: -120px;
    top: 40px;
    width: 260px;
    height: 260px;
    border-radius: 50%;
    background: var(--faint);
  }

  .lockup {
    position: absolute;
    text-align: center;
    color: var(--gold);
  }
  .lockup__dot {
    display: block;
    margin: 0 auto 22px;
    border-radius: 50%;
    background: var(--gold);
  }
  .lockup__name {
    font-family: "Marcellus", serif;
    font-size: 50px;
    letter-spacing: 12px;
    line-height: 1;
    padding-left: 12px;
  }
  .lockup__since {
    font-family: "Poppins", sans-serif;
    font-weight: 400;
    font-size: 15px;
    letter-spacing: 6px;
    margin-top: 10px;
  }

  .card--front .lockup { left: 0; right: 0; top: 70px; }
  .card--front .lockup__dot { width: 110px; height: 110px; }

  .card--back .lockup { left: 44px; top: 44px; text-align: left; }
  .card--back .lockup__name { font-size: 46px; padding-left: 0; }
  .card--back .lockup__since { padding-left: 70px; }

  .feature-dot {
    position: absolute;
    right: 60px;
    top: 110px;
    width: 210px;
    height: 210px;
    border-radius: 50%;
    background: var(--gold-soft);
  }

  .contact {
    position: absolute;
    left: 44px;
    top: 180px;
    color: var(--gold);
  }
  .contact__name {
    font-family: "Cormorant Garamond", serif;
    font-weight: 600;
    font-size: 27px;
    margin: 0 0 4px;
  }
  .contact__role {
    font-family: "Poppins", sans-serif;
    font-weight: 300;
    font-size: 14px;
    line-height: 1.4;
    margin: 0 0 14px;
  }
  .contact__list {
    list-style: none;
    margin: 0;
    padding: 0;
    font-family: "Poppins", sans-serif;
    font-weight: 300;
    font-size: 14px;
  }
  .contact__list li {
    display: flex;
    align-items: center;
    gap: 8px;
    margin-bottom: 5px;
  }
  .contact__icon { width: 12px; height: 12px; fill: var(--gold); }
</style>
</head>
<body>
<main class="canvas">

  <section class="card card--front" aria-label="Card front">
    <div class="faint-mark"></div>
    <div class="lockup">
      <span class="lockup__dot"></span>
      <div class="lockup__name">TALMORK</div>
      <div class="lockup__since">SINCE 2026</div>
    </div>
  </section>

  <section class="card card--back" aria-label="Card back">
    <div class="lockup">
      <div class="lockup__name">TALMORK</div>
      <div class="lockup__since">SINCE 2026</div>
    </div>

    <div class="contact">
      <p class="contact__name">Talmork Brekkestad</p>
      <p class="contact__role">CEO &amp; Founder<br>Arne Olav Brekkestad</p>
      <ul class="contact__list">
        <li>
          <svg class="contact__icon" viewBox="0 0 12 12"><path d="M1 4c0-2 2-3 5-3s5 1 5 3l-2 1-1-2H4L3 5zM2 6h8l1 5H1z"/></svg>
          004791462057
        </li>
        <li>
          <svg class="contact__icon" viewBox="0 0 12 12"><path d="M0 2h12v1L6 7 0 3zM0 4.5l6 4 6-4V10H0z"/></svg>
          talmork.llc@mailbox.com
        </li>
        <li>
          <svg class="contact__icon" viewBox="0 0 12 12"><circle cx="6" cy="6" r="5.5" fill="none" stroke="currentColor" style="stroke:var(--gold)" stroke-width="1.2"/><path d="M0.5 6h11M6 0.5c-3 3-3 8 0 11M6 0.5c3 3 3 8 0 11" fill="none" style="stroke:var(--gold)" stroke-width="1"/></svg>
          www.talmork.llc
        </li>
      </ul>
    </div>

    <div class="feature-dot"></div>
  </section>

</main>
</body>
</html>
```